Business Cards - Brightpath Horizon

need to design unique business card for my mortgage business. I need to design credit card style business card for my business or any unique idea that you might have

Target Market(s)

Home Loan customers

Industry/Entity Type

Mortgage Brokerage

Contact Information for Business Card

please design credit card style or very unique style business card

Colors

Designer to choose colors to be used in the design.

Requirements
Must have
• Name
• position
• Phone number
• fax number
• email address
• website address
• social media address
• All above fields will be provided once design in finalised

```html
<!DOCTYPE html>
<html lang="en">
<head>
<meta charset="utf-8">
<title>Brightpath Horizon – Business Cards</title>
<link rel="stylesheet" href="https://fonts.googleapis.com/css2?family=Roboto+Slab:wght@400;700&family=Roboto:wght@400&family=Lora:ital@1&display=swap">
<style>
  :root {
    --stage: #e6e9ec;
    --sky-light: #2bb9f1;
    --sky-deep: #16a6ea;
    --foliage: rgba(255,255,255,0.10);
    --paper: #fbfbfb;
    --brand-blue: #1f3fb8;
    --brand-orange: #f08a1c;
    --social-blue: #2346c0;
    --white: #ffffff;
  }
  * { margin: 0; padding: 0; box-sizing: border-box; }
  html, body { width: 1200px; height: 911px; overflow: hidden; }
  body { background: var(--stage); position: relative; font-family: "Roboto Slab", serif; }

  .card {
    position: absolute;
    width: 620px;
    height: 354px;
    border-radius: 4px;
    box-shadow: 0 10px 28px rgba(0,0,0,0.18);
    overflow: hidden;
  }

  /* Contact side */
  .card--contact {
    left: 80px; top: 100px;
    background: linear-gradient(135deg, var(--sky-light), var(--sky-deep));
    color: var(--white);
  }
  .foliage {
    position: absolute; left: 150px; top: 150px; width: 300px; height: 200px;
    background: radial-gradient(ellipse at center, var(--foliage), transparent 70%);
  }
  .holder { position: absolute; left: 44px; top: 178px; }
  .holder__name { font-weight: 700; font-size: 22px; letter-spacing: 0.5px; }
  .holder__role { font-weight: 700; font-size: 15px; letter-spacing: 0.5px; margin-top: 2px; }
  .holder__rule { position: absolute; left: 44px; top: 236px; width: 320px; height: 2px; background: var(--white); }

  .hotline {
    position: absolute; right: 44px; top: 150px;
    font-family: "Roboto", sans-serif; font-size: 42px; letter-spacing: 1px;
  }
  .address {
    position: absolute; right: 44px; top: 214px; text-align: right;
    font-size: 14px; line-height: 1.45;
  }
  .details {
    position: absolute; left: 250px; top: 268px;
    font-size: 14px; line-height: 1.4;
  }

  /* Brand side */
  .card--brand {
    left: 540px; top: 470px;
    width: 580px; height: 331px;
    background: var(--paper);
  }
  .brand { position: absolute; left: 0; right: 0; top: 110px; text-align: center; }
  .brand__name {
    font-weight: 700; font-size: 40px; color: var(--brand-blue); letter-spacing: 1px;
    display: inline-flex; align-items: center; gap: 14px;
  }
  .brand__dot { width: 18px; height: 18px; border-radius: 50%; background: var(--brand-orange); }
  .brand__tagline {
    font-family: "Lora", serif; font-style: italic; font-size: 20px;
    color: var(--brand-orange); margin-top: 10px;
  }
  .social { position: absolute; right: 36px; bottom: 30px; display: flex; gap: 8px; }
  .social__dot { width: 22px; height: 22px; border-radius: 50%; background: var(--social-blue); }
</style>
</head>
<body>
  <section class="card card--contact">
    <div class="foliage" role="img" aria-label="Faint tree foliage texture"></div>
    <div class="holder">
      <div class="holder__name">DANIEL REYES</div>
      <div class="holder__role">CEO/FOUNDER</div>
    </div>
    <div class="holder__rule"></div>
    <div class="hotline">555 204 3178</div>
    <div class="address">2140 Maple Ridge Road<br>Juneau, Alaska 99801</div>
    <div class="details">
      P. 555 610 4482<br>
      hello@brightpath.com<br>
      www.brightpath.com
    </div>
  </section>

  <section class="card card--brand">
    <div class="brand">
      <div class="brand__name"><span class="brand__dot"></span>Brightpath Horizon</div>
      <div class="brand__tagline">Clear choices, Open doors</div>
    </div>
    <div class="social" aria-label="Social media links">
      <span class="social__dot"></span>
      <span class="social__dot"></span>
      <span class="social__dot"></span>
      <span class="social__dot"></span>
    </div>
  </section>
</body>
</html>
```